Copper Ridge Inquiries Letterhead

I would like to design a letterhead for a private investigation company. Our primary clients will be law firms. The business card is included below

```html
<!DOCTYPE html>
<html lang="en">
<head>
<meta charset="utf-8">
<title>Copper Ridge Inquiries Letterhead</title>
<link rel="stylesheet" href="https://fonts.googleapis.com/css2?family=Lato:wght@400&family=Montserrat:wght@400;700&family=Open+Sans:wght@400&display=swap">
<style>
  :root {
    --navy: #1c355e;
    --orange: #f05f2f;
    --ink: #1b1b1b;
    --paper: #ffffff;
    --backdrop: #e4e4e4;
    --sig-tone: #ececec;
  }
  * { margin: 0; padding: 0; box-sizing: border-box; }
  html, body {
    width: 1200px; height: 1079px; overflow: hidden;
    background: var(--backdrop);
  }
  .letterhead {
    position: absolute; left: 240px; top: 30px;
    width: 720px; height: 1019px;
    background: var(--paper);
    box-shadow: 0 4px 14px rgba(0,0,0,.18);
    overflow: hidden;
  }
  .brand {
    position: absolute; left: 37px; top: 120px;
    display: flex; align-items: center; gap: 10px;
  }
  .brand-dot {
    width: 26px; height: 26px; border-radius: 50%;
    background: var(--orange); flex: none;
  }
  .brand-name {
    font-family: "Montserrat", sans-serif; font-weight: 700;
    font-size: 21px; line-height: 1.05; color: var(--navy);
    text-transform: uppercase; letter-spacing: .2px;
  }
  .contact {
    position: absolute; left: 361px; top: 80px;
    font-family: "Montserrat", sans-serif; font-size: 13.4px;
    color: #2a2a2a; text-transform: uppercase; list-style: none;
  }
  .contact li { display: flex; align-items: center; height: 18px; }
  .contact svg { width: 11px; height: 11px; margin-right: 7px; fill: var(--orange); flex: none; }
  .license { margin-top: 7px; }
  .body-copy {
    position: absolute; left: 37px; top: 337px; width: 648px;
    font-family: "Lato", sans-serif; font-size: 10.3px; line-height: 15.8px;
    color: var(--ink); text-align: justify; hyphens: auto;
  }
  .body-copy p + p { margin-top: 15px; }
  .closing {
    position: absolute; left: 37px; top: 714px;
    font-family: "Open Sans", sans-serif; font-size: 20px; color: var(--ink);
  }
  .signature {
    position: absolute; left: 37px; top: 764px;
    width: 156px; height: 34px; background: var(--sig-tone); border-radius: 3px;
  }
  .footer-band { position: absolute; left: 0; bottom: 0; width: 720px; height: 25px; }
  .footer-text {
    position: absolute; left: 0; bottom: 0; width: 720px; height: 25px;
    display: flex; align-items: center; justify-content: center;
    font-family: "Montserrat", sans-serif; font-size: 12.6px; color: #fff;
    text-transform: uppercase;
  }
</style>
</head>
<body>
<main class="letterhead">
  <header>
    <div class="brand">
      <span class="brand-dot"></span>
      <span class="brand-name">Copper Ridge<br>Inquiries</span>
    </div>
    <ul class="contact">
      <li><svg viewBox="0 0 12 12"><path d="M6 0a4.2 4.2 0 0 0-4.2 4.2C1.8 7.4 6 12 6 12s4.2-4.6 4.2-7.8A4.2 4.2 0 0 0 6 0zm0 6a1.8 1.8 0 1 1 0-3.6A1.8 1.8 0 0 1 6 6z"/></svg>Fort Worth, TX</li>
      <li><svg viewBox="0 0 12 12"><path d="M1 4.5C1 2.5 3 1.5 6 1.5s5 1 5 3v1H8.5V4.2h-5v1.3H1zM3 6.5h6l1.5 4h-9z"/></svg>555.014.2290</li>
      <li><svg viewBox="0 0 12 12"><circle cx="6" cy="6" r="5.5"/><circle cx="6" cy="6" r="2" fill="#fff"/></svg>nora@copperridgeinquiries.com</li>
      <li class="license">License No. 00421736</li>
    </ul>
  </header>

  <section class="body-copy">
    <p>Lorem ipsum dolor sit amet, consectetur adipiscing elit, sed do eiusmod tempor incididunt ut labore et dolore magna aliqua. Ut enim ad minim veniam, quis nostrud exercitation ullamco laboris nisi ut aliquip ex ea commodo consequat. Duis aute irure dolor in reprehenderit in voluptate velit esse cillum dolore eu fugiat nulla pariatur.Contrary to popular belief, Lorem Ipsum is not simply random text. It has roots in a piece of classical Latin literature from 45 BC, making it over 2000 years old. Arthur Penwell, a Latin professor at Larkmoor College in Virginia, looked up one of the more obscure Latin words, consectetur, from a Lorem Ipsum passage, and going through the cites of the word in classical literature, discovered the undoubtable source.</p>
    <p>Lorem ipsum dolor sit amet, consectetur adipiscing elit, sed do eiusmod tempor incididunt ut labore et dolore magna aliqua. Ut enim ad minim veniam, quis nostrud exercitation ullamco laboris nisi ut aliquip ex ea commodo consequat. Duis aute irure dolor in reprehenderit in voluptate velit esse cillum dolore eu fugiat nulla pariatur. There are many variations of passages of Lorem Ipsum available, but the majority have suffered alteration in some form, by injected humour, or randomised words which don't look even slightly believable.</p>
    <p>Lorem ipsum dolor sit amet, consectetur adipiscing elit, sed do eiusmod tempor incididunt ut labore et dolore magna aliqua. Ut enim ad minim veniam, quis nostrud exercitation ullamco laboris nisi ut aliquip ex ea commodo consequat.Contrary to popular belief, Lorem Ipsum is not simply random text. It has roots in a piece of classical Latin literature from 45 BC, making it over 2000 years old. Arthur Penwell, a Latin professor at Larkmoor College</p>
    <p>Excepteur sint occaecat cupidatat non proident, sunt in culpa qui officia deserunt mollit anim id est laborum. re et dolore magnam aliquam quaerat voluptatem.Contrary to popular belief, Lorem Ipsum is not simply random text. It has roots in a piece of classical Latin literature from 45 BC,</p>
  </section>

  <p class="closing">Sincerely,</p>
  <div class="signature" role="img" aria-label="Handwritten signature of Dana Whitfield"></div>

  <footer>
    <svg class="footer-band" viewBox="0 0 720 25" preserveAspectRatio="none">
      <rect width="720" height="25" fill="var(--navy)"/>
      <polygon points="120,0 593,0 605,25 112,25" fill="#fff"/>
      <polygon points="124,0 590,0 600,25 117,25" fill="var(--orange)"/>
    </svg>
    <div class="footer-text">Over 20 years of investigative experince</div>
  </footer>
</main>
</body>
</html>
```